Q7 Nexa needs a standing banner

Q7 Nexa banner
We need a standing banner for Q7 Nexa (www.q7nexa.com.au).
The banner should be: 1000mm (wide) x 2200mm (high) and high resolution.
All images should be either those supplied with these specifications or Public Domain (CC0).
Templates for the banner attached (Refer StandardPullUp_Templates_1000x2200.pdf file)
About us:
We provide high quality professional services for the Australian space industry, such as consultation, contracted personnel, and project delivery. Our clients include organisations working in the space industry. We work with companies that produce communications systems, satellites, launchpad technology, space situational awareness, and Internet-of-Things (IoT) technology being developed within the space industry.
The banner will promote Q7 Nexa to potential space customers at events, trade shows, and presentations, and should be professional, visually appealing, clear, and uncluttered.
Logo:
Include the Q7 Nexa logo or the Q7 Nexa heading (both are attached).
Text:
The banner should include some text but not be too cluttered. Include some of the following text:
[Choose from the following:]
Delivering value to our clients in a manner that inspires.
Delivering excellence in Space Professional Services
Specialised Support Service Provider
Bringing exceptional talent to the Australian space sector.
[And select a sentence or two from the following:]
Our services aim to fast-track project development, pre-empt and solve problems more efficiently, and inspire and guide success.
We understand cybersecurity technologies, communications, systems engineering, systems design, facilities, integration, infrastructure, and modern systems development principles.
By leveraging our skills and experience, we understand your problems and can identify talented people both locally and internationally that deliver the solutions you need.
Q7 staff have been in the forefront of major program deliveries to defence and commercial clients across the maritime and defence market for decades.
Our staff are leaders in their field and pioneers in the establishment of systematic approaches to the most complex problems.
---
You can also see our website (www.q7nexa.com.au) for more text to choose from
However, don’t overload the banner with text – keep it to the logo, a branding statement, and a sentence or two at the most. A captivating design with imagery is what we are after.
Images:
Images should be recent, high resolution, Australian (where possible), and realistic. Images with people in a technology or Space related industry setting are good. Suggestions include professionals working in mission control stations or technical/office environments. Other images might include mission control centres, rockets, satellites, radio communications equipment, large satellite dishes, night landscapes with stars, or pictures of Australia or Earth from space. Include both graphics and photos.
NO cartoons or space shuttles from the 1980s please.
Images should be current rather than old. See our website for some example images, though you are encouraged to use images other than these.
Colours:
We would like the colours to match the Q7 Nexa logo, using mainly: navy blue (#000080) and matching blues; platinum (#E5E4E2), rocket metallic (#8A7F8D) and similar greys; black (#000000), and white (#FFFFFF). Sunlight colours may be included sparingly as a highlight.
Attached files:
- I have attached the Q7 Nexa logo which must appear on the banner (‘q7nexa.ai’)
- I have attached the Q7 Nexa heading, which may also appear on the banner (‘q7nexa-heading.psd’)
We look forward to seeing your designs!

```html
<!DOCTYPE html>
<html lang="en">
<head>
<meta charset="utf-8">
<title>Q7 Nexa – Pull-up Banner</title>
<link rel="stylesheet" href="https://fonts.googleapis.com/css2?family=Montserrat:wght@400;500;700&display=swap">
<style>
  :root {
    --bg-top: #3b2c93;
    --bg-mid: #2e2380;
    --bg-bottom: #1c1458;
    --lavender: #b9b2ee;
    --accent: #6f63c9;
    --ring: #5b4fc0;
    --white: #ffffff;
    --navy: #1a1466;
  }
  * { margin: 0; padding: 0; box-sizing: border-box; }
  html, body { width: 720px; height: 1200px; overflow: hidden; }
  body { font-family: "Montserrat", sans-serif; background: var(--bg-bottom); }
  .banner {
    position: relative;
    width: 720px;
    height: 1200px;
    background: linear-gradient(180deg, var(--bg-top) 0%, var(--bg-mid) 55%, var(--bg-bottom) 100%);
    overflow: hidden;
  }
  .graphics { position: absolute; inset: 0; }
  .brand {
    position: absolute;
    top: 50px;
    left: 290px;
    display: flex;
    align-items: center;
    gap: 16px;
    color: var(--white);
    font-weight: 700;
    font-size: 54px;
    letter-spacing: 1px;
  }
  .brand-dot {
    width: 22px; height: 22px;
    border-radius: 50%;
    background: var(--white);
  }
  .statement {
    position: absolute;
    top: 762px;
    left: 48px;
    padding-left: 26px;
    border-left: 8px solid var(--lavender);
  }
  .headline {
    color: var(--white);
    font-weight: 700;
    font-size: 43px;
    line-height: 1.13;
  }
  .body-copy {
    position: absolute;
    top: 978px;
    left: 82px;
    width: 500px;
    color: var(--white);
    font-weight: 400;
    font-size: 19px;
    line-height: 1.45;
  }
  .web-pill {
    position: absolute;
    top: 1106px;
    left: 48px;
    width: 440px;
    height: 56px;
    border-radius: 28px;
    background: var(--white);
    color: var(--navy);
    font-weight: 700;
    font-size: 27px;
    display: flex;
    align-items: center;
    justify-content: center;
  }
</style>
</head>
<body>
<div class="banner">
  <svg class="graphics" width="720" height="1200" viewBox="0 0 720 1200">
    <defs>
      <linearGradient id="roomBase" x1="0" y1="0" x2="0" y2="1">
        <stop offset="0" stop-color="#1b2a4c"/>
        <stop offset="0.45" stop-color="#2c4a7a"/>
        <stop offset="0.75" stop-color="#14203c"/>
        <stop offset="1" stop-color="#080d1c"/>
      </linearGradient>
      <radialGradient id="screenGlow" cx="0.5" cy="0.32" r="0.55">
        <stop offset="0" stop-color="#8fb4e6" stop-opacity="0.75"/>
        <stop offset="0.5" stop-color="#4a6fa8" stop-opacity="0.35"/>
        <stop offset="1" stop-color="#0c1226" stop-opacity="0"/>
      </radialGradient>
      <radialGradient id="operatorTone" cx="0.45" cy="0.6" r="0.65">
        <stop offset="0" stop-color="#e0602a"/>
        <stop offset="0.3" stop-color="#b6532a"/>
        <stop offset="0.55" stop-color="#6a5a74"/>
        <stop offset="1" stop-color="#e4e7ee"/>
      </radialGradient>
    </defs>
    <path class="sweep-accent" d="M270 138 C95 138 28 262 28 420 C28 585 118 700 270 724" fill="none" stroke="#6f63c9" stroke-width="6"/>
    <path class="sweep-line" d="M258 150 C108 150 44 262 44 420 C44 575 126 690 262 712" fill="none" stroke="#ffffff" stroke-width="8"/>
    <g role="img" aria-label="Mission control room with staff working at consoles in front of large wall screens">
      <path d="M720 164 H250 C122 164 62 266 62 420 C62 560 134 680 262 698 H720 Z" fill="url(#roomBase)"/>
      <path d="M720 164 H250 C122 164 62 266 62 420 C62 560 134 680 262 698 H720 Z" fill="url(#screenGlow)"/>
    </g>
    <circle cx="588" cy="650" r="128" fill="#5b4fc0"/>
    <circle cx="588" cy="650" r="116" fill="#ffffff"/>
    <circle class="inset-photo" role="img" aria-label="Technician in orange working in a bright technical facility"
            cx="588" cy="650" r="106" fill="url(#operatorTone)"/>
  </svg>

  <div class="brand"><span class="brand-dot"></span>Q7 Nexa</div>

  <div class="statement">
    <h1 class="headline">Bringing<br>exceptional talent<br>to the Australian<br>space sector</h1>
  </div>

  <p class="body-copy">Q7 staff have been in the forefront of major program deliveries to defence and commercial clients across the maritime and defence market for decades.</p>

  <div class="web-pill">www.q7nexa.com.au</div>
</div>
</body>
</html>
```